Behavioral Health Booth Backdrop Design

I need a design created for our backdrop as we are purchasing a new curved 10x10 backdrop for our trade shows. We are a behavioral health (mental health and addiction services) agency and want something that catches your eye when walking by. We don't want a lot of "words" or description on it, but more of a catchy look. I have attached some pics that we like the colors of in general (abstract). This doesn't mean that you need to use these specific pics. I have also attached our Logo with our name.

Requirements
Must have
• Eye catchy design and or a picture/photo with our agency name and/or logo on the backdrop. One of the files to be a vector file.

```html
<!DOCTYPE html>
<html lang="en">
<head>
<meta charset="utf-8">
<title>Orvane Glen Behavioral Health Solutions – Booth Backdrop</title>
<link rel="stylesheet" href="https://fonts.googleapis.com/css2?family=Bebas+Neue&family=Lobster+Two:ital,wght@1,700&family=Tinos&display=swap">
<style>
  :root {
    --mat: #dcdedd;
    --orange-deep: #ef7a1e;
    --orange-mid: #f6a21c;
    --orange-light: #fcc52a;
    --ink: #2b2b2b;
    --white: #ffffff;
  }
  * { margin: 0; padding: 0; box-sizing: border-box; }
  html, body {
    width: 1192px;
    height: 1200px;
    overflow: hidden;
    background: var(--mat);
  }
  .backdrop {
    position: absolute;
    left: 45px;
    top: 50px;
    width: 1102px;
    height: 1102px;
    overflow: hidden;
    background: linear-gradient(135deg, var(--orange-deep) 0%, var(--orange-mid) 45%, var(--orange-light) 100%);
  }
  .backdrop-art {
    position: absolute;
    inset: 0;
    width: 100%;
    height: 100%;
  }
  .brand {
    position: absolute;
    left: 270px;
    top: 82px;
    display: flex;
    align-items: center;
    gap: 16px;
    color: var(--white);
    font-family: "Tinos", serif;
  }
  .brand-mark {
    width: 110px;
    height: 110px;
    border-radius: 50%;
    background: var(--white);
    flex: none;
  }
  .brand-name {
    display: flex;
    flex-direction: column;
    line-height: 1;
    padding-top: 20px;
  }
  .brand-title {
    font-size: 56px;
    letter-spacing: 1px;
  }
  .brand-sub {
    font-size: 24px;
    letter-spacing: 0.6px;
    margin-top: 0;
  }
  .headline {
    position: absolute;
    left: 0;
    right: 0;
    top: 272px;
    text-align: center;
    font-family: "Bebas Neue", sans-serif;
    font-weight: 400;
    font-size: 86px;
    line-height: 89px;
    color: var(--ink);
    letter-spacing: 1px;
  }
  .tagline {
    position: absolute;
    left: 0;
    right: 0;
    top: 528px;
    text-align: center;
    font-family: "Lobster Two", cursive;
    font-style: italic;
    font-weight: 700;
    font-size: 66px;
    line-height: 1.1;
    color: var(--white);
  }
</style>
</head>
<body>
  <main class="backdrop">
    <svg class="backdrop-art" viewBox="0 0 1102 1102" xmlns="http://www.w3.org/2000/svg">
      <defs>
        <linearGradient id="shard-warm" x1="0" y1="0" x2="1" y2="1">
          <stop offset="0" stop-color="#fcc52a"/>
          <stop offset="1" stop-color="#ee6f1c"/>
        </linearGradient>
        <linearGradient id="shard-bright" x1="1" y1="0" x2="0" y2="1">
          <stop offset="0" stop-color="#fdd030"/>
          <stop offset="1" stop-color="#f08a20"/>
        </linearGradient>
      </defs>
      <g role="img" aria-label="Abstract low-poly shards in orange and yellow, lower left">
        <path d="M0 470 L230 480 L330 620 L450 860 L470 1102 L0 1102 Z" fill="url(#shard-warm)"/>
      </g>
      <g role="img" aria-label="Abstract shard, top right corner">
        <path d="M1010 0 L1102 0 L1102 60 L1045 180 Z" fill="url(#shard-bright)"/>
      </g>
      <g role="img" aria-label="Abstract shard, right edge">
        <path d="M1102 470 L1060 540 L1102 640 Z" fill="url(#shard-bright)"/>
      </g>
      <g role="img" aria-label="Abstract shard, bottom right">
        <path d="M1000 1102 L1060 990 L1102 1102 Z" fill="url(#shard-warm)"/>
      </g>
      <circle class="faint-disc" cx="825" cy="845" r="250" fill="#fcc52a" opacity="0.35"/>
    </svg>

    <div class="brand">
      <span class="brand-mark"></span>
      <div class="brand-name">
        <span class="brand-title">ORVANE GLEN</span>
        <span class="brand-sub">BEHAVIORAL HEALTH SOLUTIONS</span>
      </div>
    </div>

    <h1 class="headline">Comprehensive<br>mental health and<br>addiction services.</h1>
    <p class="tagline">Where hope begins.</p>
  </main>
</body>
</html>
```